Dalvick's Business Card

I need some designs for a new business card including the new logo attached. An old example of our business card is also attached to show all the data that should be included on the new design.
**I added some more examples someone had mocked up**

Contact Information for Business Card

Should include all info on other examples uploaded.

```html
<!DOCTYPE html>
<html lang="en">
<head>
<meta charset="utf-8">
<title>Dalvick's Business Card</title>
<link href="https://fonts.googleapis.com/css2?family=Montserrat:wght@400;500;800&display=swap" rel="stylesheet">
<style>
  :root {
    --brand-blue: #0b72b9;
    --brand-red: #ea1f2a;
    --paper: #ffffff;
    --backdrop: #e6e6e8;
  }
  * { margin: 0; padding: 0; box-sizing: border-box; }
  html, body {
    width: 1200px; height: 1200px; overflow: hidden;
    background: var(--backdrop);
    font-family: "Montserrat", sans-serif;
  }
  .sheet {
    width: 1200px; height: 1200px;
    display: flex; flex-direction: column; align-items: center; justify-content: center;
    gap: 56px;
  }
  .card {
    position: relative; width: 900px; height: 514px; overflow: hidden;
    box-shadow: 0 18px 40px rgba(0,0,0,0.25);
  }
  .card-shapes { position: absolute; inset: 0; }

  /* Front */
  .card-front { background: var(--brand-blue); }
  .band-text {
    position: absolute; left: 0; right: 0;
    color: var(--paper); font-weight: 500; text-transform: uppercase;
    text-align: center; letter-spacing: 0.5px; white-space: nowrap;
  }
  .band-top { top: 24px; font-size: 30px; }
  .band-bottom { bottom: 24px; font-size: 21px; }
  .front-brand {
    position: absolute; left: 0; right: 0; top: 210px;
    display: flex; align-items: center; justify-content: center; gap: 22px;
  }
  .brand-dot { width: 62px; height: 62px; border-radius: 50%; background: var(--paper); }
  .brand-name {
    font-size: 82px; font-weight: 500; letter-spacing: 2px; color: var(--paper);
    text-transform: uppercase; line-height: 1; white-space: nowrap;
  }

  /* Back */
  .card-back { background: var(--paper); }
  .back-brand {
    position: absolute; left: 60px; top: 110px;
    display: flex; align-items: center; gap: 14px;
  }
  .back-brand .brand-dot { width: 38px; height: 38px; background: var(--brand-blue); }
  .back-brand .brand-name { font-size: 44px; color: var(--brand-blue); }
  .holder-name {
    position: absolute; right: 40px; top: 80px;
    color: var(--paper); font-size: 34px; font-weight: 800; text-transform: uppercase;
    white-space: nowrap; line-height: 1.1;
  }
  .contact-list {
    position: absolute; right: 40px; top: 220px; list-style: none;
    color: var(--paper); text-align: right; font-size: 20px; line-height: 1.45;
  }
  .contact-list li {
    display: flex; align-items: center; justify-content: flex-end; gap: 10px;
    white-space: nowrap;
  }
  .contact-list svg { width: 20px; height: 20px; }
  .contact-list .credential { text-transform: uppercase; }
  .contact-list .credential-first { margin-top: 14px; }
</style>
</head>
<body>
<main class="sheet">

  <section class="card card-front" aria-label="Card front">
    <svg class="card-shapes" viewBox="0 0 900 514" aria-hidden="true">
      <path fill="var(--brand-red)" d="M0 0H900V88H380L350 108L320 88H0Z"/>
      <path fill="var(--brand-red)" d="M0 426H540L570 406L600 426H900V514H0Z"/>
    </svg>
    <p class="band-text band-top">Serves Ridgefield, IA &amp; Surrounding Areas</p>
    <div class="front-brand">
      <span class="brand-dot"></span>
      <span class="brand-name">Dalvick's</span>
    </div>
    <p class="band-text band-bottom">Call today for all your HVAC, refrigeration &amp; plumbing needs</p>
  </section>

  <section class="card card-back" aria-label="Card back">
    <svg class="card-shapes" viewBox="0 0 900 514" aria-hidden="true">
      <path fill="var(--brand-blue)" d="M580 0C460 60 450 200 450 300C450 400 450 470 380 514H900V0Z"/>
      <path fill="var(--brand-red)" d="M600 0C480 60 470 200 470 300C470 400 470 470 400 514H900V0Z"/>
    </svg>
    <div class="back-brand">
      <span class="brand-dot"></span>
      <span class="brand-name">Dalvick's</span>
    </div>
    <h1 class="holder-name">Steve Dalvick</h1>
    <ul class="contact-list">
      <li>555.014.2290
        <svg viewBox="0 0 24 24" aria-hidden="true"><path fill="#fff" d="M6.6 10.8a15 15 0 0 0 6.6 6.6l2.2-2.2c.3-.3.7-.4 1-.2 1.1.4 2.3.6 3.6.6.6 0 1 .4 1 1V20c0 .6-.4 1-1 1A17 17 0 0 1 3 4c0-.6.4-1 1-1h3.5c.6 0 1 .4 1 1 0 1.3.2 2.5.6 3.6.1.3 0 .7-.2 1Z"/></svg>
      </li>
      <li>hvacdalvick@mailbox.com
        <svg viewBox="0 0 24 24" aria-hidden="true"><path fill="#fff" d="M2 5h20v14H2Zm2 2v.5l8 5 8-5V7l-8 5Z"/></svg>
      </li>
      <li class="credential credential-first">Licensed &amp; Insured</li>
      <li class="credential">Family Owned &amp; Operated</li>
    </ul>
  </section>

</main>
</body>
</html>
```